Talvique Hotels Business Card and Logo

We need a business card design for a hotel group. I saw a hotel card you designed and really liked it. We have multiple properties with different brands. Were hoping that the card would be unique and find a way to list out all our properties. Our web address is www.talviquehotels.com. I have attached some photos of card designs I like.

Industry/Entity Type

Hotel

Contact Information for Business Card

Scott CurranReneson HotelsChief Operating Officer56 Madera DriveCorte Madera, CA 94925Office 415-891-5013Cell 707-5550143

```html
<!DOCTYPE html>
<html lang="en">
<head>
<meta charset="utf-8">
<title>Talvique Hotels — Business Card</title>
<link rel="stylesheet" href="https://fonts.googleapis.com/css2?family=Cinzel:wght@500&family=Montserrat:wght@400;500&display=swap">
<style>
  :root {
    --page-bg: #e7e5e2;
    --card-back: #58585b;
    --card-back-ink: #444447;
    --card-front: #f7f7f6;
    --copper: #bf642d;
    --ink-dark: #4a4a4c;
    --ink-mid: #6d6d70;
    --rule: #a9a9ab;
  }
  * { margin: 0; padding: 0; box-sizing: border-box; }
  html, body {
    width: 1200px;
    height: 985px;
    overflow: hidden;
    background: var(--page-bg);
  }
  .canvas {
    position: relative;
    width: 1200px;
    height: 985px;
  }
  .card {
    position: absolute;
    left: 250px;
    width: 700px;
    height: 400px;
    display: flex;
    flex-direction: column;
    align-items: center;
    box-shadow: 0 2px 6px rgba(0,0,0,0.12);
  }
  .card--back {
    top: 70px;
    background: var(--card-back);
    justify-content: center;
  }
  .card--front {
    top: 515px;
    background: var(--card-front);
    padding-top: 52px;
  }
  .brand-mark {
    width: 58px;
    height: 58px;
    margin-bottom: 16px;
  }
  .card--back .brand-mark { background: var(--card-back-ink); }
  .card--front .brand-mark { background: var(--copper); }
  .brand-name {
    font-family: "Montserrat", sans-serif;
    font-weight: 500;
    font-size: 34px;
    letter-spacing: 1.5px;
    text-transform: uppercase;
  }
  .card--back .brand-name { color: var(--card-back-ink); }
  .card--front .brand-name { color: var(--copper); }
  .person-name {
    margin-top: 26px;
    font-family: "Cinzel", serif;
    font-weight: 500;
    font-size: 25px;
    letter-spacing: 1.5px;
    color: var(--ink-dark);
  }
  .person-title {
    margin-top: 2px;
    font-family: "Montserrat", sans-serif;
    font-weight: 400;
    font-size: 15px;
    letter-spacing: 1px;
    color: var(--ink-mid);
    text-transform: uppercase;
  }
  .divider {
    width: 400px;
    height: 1px;
    background: var(--rule);
    margin: 12px 0 10px;
  }
  .contact-line {
    font-family: "Montserrat", sans-serif;
    font-weight: 400;
    font-size: 15px;
    letter-spacing: 1px;
    line-height: 1.45;
    color: var(--ink-mid);
    text-transform: uppercase;
  }
  .sep { margin: 0 8px; }
</style>
</head>
<body>
<main class="canvas">
  <section class="card card--back" aria-label="Card back">
    <div class="brand-mark"></div>
    <p class="brand-name">Talvique Hotels</p>
  </section>

  <section class="card card--front" aria-label="Card front">
    <div class="brand-mark"></div>
    <p class="brand-name">Talvique Hotels</p>
    <p class="person-name">BRENT HOLLOWAY</p>
    <p class="person-title">Chief Operating Officer</p>
    <div class="divider"></div>
    <p class="contact-line">83 Pellwick Lane, Larkfield Bay, CA 94817</p>
    <p class="contact-line">Office 415-555-0186<span class="sep">|</span>Cell 707-5550143</p>
  </section>
</main>
</body>
</html>
```